Need Primer (paint) Label Design

THE ATTACHED LABEL/S ARE SOLEY FOR REFERENCE. DO NOT MAKE ME AN INTERIOR PAINT OR CHALK PAINT LABEL. I ONLY NEED A "PRIMER" LABEL. THE ATTACHED INTERIOR PAINT LABEL IS ONLY TO SHOW YOU THE THEME/DESIGN OF OUR OTHER LABELS. THE BLUE LABEL ONLY HAS A DESIGN ASPECT I LIKE (PRIMER ON SIDE). The last four labels are our competitors.
```````````````````````````````````````````````````````````````````````````````````````````````````
We need this label to look professional, sharp, eye catching and modern.
OUR PRIMARY COLORS ARE BLACK AND WHITE. IF YOU INCOPORATE ANOTHER COLOR, SILVER OR GOLD MIGHT BE IDEAL BUT PLEASE DON'T DRIFT TOO FAR.
The attached documents:
1st - Our Logo
2nd - Our chalk paint label (reference). We do not need a chalk paint label.
3rd. A random design example. I like the PRIME on the side running vertically. I think it's a cool design concept.
````````````````````````````````````````````````````````````````````````````````````````````````````
We are going to be using a normal paint can with a metal bail/handle so please use that with you design work
``````````````````````````````````````````````````````````````````````````````````````````````````
Order, in my head:
4376
Coatings
^^ I want this to stand out as well but I don't want it to be the first thing your eye is drawn to. Probably 2nd
Interior/Exterior
Multi - Surface Primer
^^ Want this to stick out and draw your eye so the customer knows what it is immediately
Exceptional Adhesion, Performance, Durability,
Use on Wood, Drywall, Plaster, Stucco, Masonry, Brick, Paneling, Painted Metal, & Properly Prepared Glossy Surfaces & More
35* Lowe Temperature Application (can be on side or small)
100% Acrylic
Low Odor - Low VOC - Soap & Water Clean Up
1 US Gallon - 3.785 L
Feel free to get creative with it!

```html
<!DOCTYPE html>
<html lang="en">
<head>
<meta charset="utf-8">
<title>4376 Coatings – Multi-Surface Primer Label</title>
<link rel="stylesheet" href="https://fonts.googleapis.com/css2?family=Montserrat:wght@300;500;600;700;800&display=swap">
<style>
  :root {
    --page-bg: #f4f4f4;
    --label-black: #0a0a0a;
    --label-white: #ffffff;
    --accent-gold: #c9a96a;
  }
  html, body {
    margin: 0;
    padding: 0;
    width: 710px;
    height: 1200px;
    overflow: hidden;
    background: var(--page-bg);
  }
  .canvas {
    position: relative;
    width: 710px;
    height: 1200px;
  }
  .primer-label {
    position: absolute;
    left: 45px;
    top: 308px;
    width: 620px;
    height: 584px;
    background: var(--label-black);
    box-shadow: 6px 8px 10px rgba(0,0,0,0.28);
  }
  .primer-label svg {
    display: block;
    width: 620px;
    height: 584px;
  }
  .label-text {
    font-family: 'Montserrat', sans-serif;
    fill: var(--label-white);
  }
  .brand-mark { font-weight: 500; }
  .headline { font-weight: 700; }
  .feature { font-weight: 700; font-size: 11.5px; }
  .claims { font-weight: 700; font-size: 12.5px; }
  .surfaces { font-weight: 500; font-size: 10.5px; }
  .stat-big { font-weight: 800; }
  .stat-small { font-weight: 700; font-size: 6.5px; }
  .volume { font-weight: 700; font-size: 13.5px; }
  .acrylic { font-weight: 300; font-size: 18px; }
  .product-type { font-weight: 500; }
  .product-name { font-weight: 700; }
  .frame-line { stroke: var(--label-white); fill: none; }
  .accent-dot { fill: var(--accent-gold); }
</style>
</head>
<body>
<main class="canvas">
  <section class="primer-label" aria-label="4376 Coatings multi-surface primer label">
    <svg viewBox="0 0 620 584" xmlns="http://www.w3.org/2000/svg">
      <!-- brand panel frame -->
      <rect class="frame-line" x="29" y="24" width="399" height="414" stroke-width="2"/>

      <!-- brand name -->
      <text class="label-text brand-mark" x="59" y="205" font-size="220" textLength="344" lengthAdjust="spacingAndGlyphs">4376</text>
      <text class="label-text brand-mark" x="63" y="270" font-size="62" textLength="337" lengthAdjust="spacing">COATINGS</text>

      <!-- use line -->
      <line class="frame-line" x1="64" y1="299" x2="400" y2="299" stroke-width="1.5"/>
      <text class="label-text headline" x="63" y="337" font-size="28" textLength="337" lengthAdjust="spacingAndGlyphs">INTERIOR/EXTERIOR</text>
      <line class="frame-line" x1="64" y1="350" x2="400" y2="350" stroke-width="1.5"/>

      <!-- feature row -->
      <g text-anchor="middle">
        <text class="label-text feature" x="106" y="374">EXCEPTIONAL</text>
        <text class="label-text feature" x="106" y="387">ADHESION</text>
        <text class="label-text feature" x="236" y="381">PERFORMANCE</text>
        <text class="label-text feature" x="354" y="381">DURABILITY</text>
        <text class="label-text claims" x="231" y="418">LOW ODOR - LOW VOC - SOAP &amp; WATER CLEAN UP</text>
      </g>
      <line class="frame-line" x1="169" y1="355" x2="169" y2="396" stroke-width="1.5"/>
      <line class="frame-line" x1="302" y1="355" x2="302" y2="396" stroke-width="1.5"/>

      <!-- surfaces -->
      <g text-anchor="middle">
        <text class="label-text surfaces" x="229" y="466">USE ON WOOD  •  DRYWALL  •  PLASTER  •</text>
        <text class="label-text surfaces" x="229" y="480">STUCCO  •  MASONRY  •  BRICK  •  PANELING  •  PAINTED METAL  •</text>
        <text class="label-text surfaces" x="229" y="494">&amp; PROPERLY PREPARED GLOSSY SURFACES &amp; MORE</text>
      </g>

      <!-- spec row -->
      <g text-anchor="middle">
        <text class="label-text stat-big" x="106" y="533" font-size="26">35*</text>
        <text class="label-text stat-small" x="106" y="547">LOWE TEMPERATURE</text>
        <text class="label-text stat-small" x="106" y="555">APPLICATION</text>
        <text class="label-text volume" x="231" y="539">1 US GALLON</text>
        <text class="label-text volume" x="231" y="555">3.785 L</text>
        <text class="label-text stat-big" x="358" y="532" font-size="27">100%</text>
        <text class="label-text acrylic" x="358" y="554">ACRYLIC</text>
      </g>
      <line class="frame-line" x1="165" y1="511" x2="165" y2="563" stroke-width="1.5"/>
      <line class="frame-line" x1="299" y1="511" x2="299" y2="563" stroke-width="1.5"/>

      <!-- vertical product name -->
      <text class="label-text product-type" transform="translate(482,340) rotate(-90)" font-size="37" textLength="295" lengthAdjust="spacingAndGlyphs">MULTI - SURFACE</text>
      <circle class="accent-dot" cx="466" cy="372" r="17"/>
      <text class="label-text product-name" transform="translate(574,553) rotate(-90)" font-size="142" textLength="511" lengthAdjust="spacingAndGlyphs">Primer</text>
    </svg>
  </section>
</main>
</body>
</html>
```